New business card/stationary for a consulting company

I am looking for a clean and very professional looking business card for my consulting company as well as corresponding stationary. I am uploading our logo. I like simple and powerful for the feel. No graphics but I am open on everything else. Below is my contact information but would like the final to be in a version I can add my employees information into and print. Thank you.

Daniel Whitcombe
dan@ferncliffadvisory.com
2870 North 9th Avenue, Summit Floor, Elm Ridge, Illinois 60531
www.ferncliffadvisory.com

Industry/Entity Type

Consulting

Contact Information for Business Card

Daniel Whitcombe
dan@ferncliffadvisory.com
www.ferncliffadvisory.com

Font styles to use
Serif
Sans Serif

Requirements
Must have
• Our logo and the business card details.
Nice to have
• our website www.ferncliffadvisory.com

```html
<!DOCTYPE html>
<html lang="en">
<head>
<meta charset="utf-8">
<title>Ferncliff Advisory – Business Card</title>
<link rel="stylesheet" href="https://fonts.googleapis.com/css2?family=Montserrat:wght@300;400;500;700&display=swap">
<style>
  :root {
    --page-bg: #efefef;
    --card-navy: #1e1e84;
    --ink-white: #ffffff;
  }
  * { margin: 0; padding: 0; box-sizing: border-box; }
  html, body {
    width: 1200px;
    height: 1000px;
    overflow: hidden;
    background: var(--page-bg);
    font-family: "Montserrat", sans-serif;
  }
  .card {
    position: absolute;
    left: 100px;
    top: 215px;
    width: 1000px;
    height: 570px;
    background: var(--card-navy);
    color: var(--ink-white);
  }
  .brand {
    position: absolute;
    right: 120px;
    top: 150px;
    display: flex;
    align-items: center;
    gap: 18px;
  }
  .brand-mark {
    width: 22px;
    height: 22px;
    background: var(--ink-white);
  }
  .brand-name {
    font-family: "Montserrat", sans-serif;
    font-weight: 300;
    font-size: 44px;
    letter-spacing: 4px;
    text-transform: uppercase;
    line-height: 1;
  }
  .identity {
    position: absolute;
    top: 262px;
    left: 0;
    width: 500px;
    text-align: right;
  }
  .person-name {
    font-weight: 700;
    font-size: 30px;
    line-height: 1.1;
  }
  .person-title {
    font-weight: 300;
    font-size: 20px;
    margin-top: 2px;
  }
  .divider-bar {
    position: absolute;
    left: 525px;
    top: 272px;
    width: 3px;
    height: 62px;
    background: var(--ink-white);
  }
  .contacts {
    position: absolute;
    left: 552px;
    top: 270px;
    list-style: none;
    font-size: 21px;
    font-weight: 400;
  }
  .contacts li {
    display: flex;
    align-items: center;
    gap: 12px;
    height: 32px;
  }
  .contacts strong { font-weight: 500; }
  .contacts svg { width: 17px; height: 17px; flex: none; }
  .rule {
    position: absolute;
    left: 70px;
    right: 70px;
    top: 400px;
    height: 2px;
    background: var(--ink-white);
  }
  .address {
    position: absolute;
    left: 70px;
    top: 438px;
    font-size: 24px;
    font-weight: 500;
    letter-spacing: 0.3px;
  }
</style>
</head>
<body>
  <main class="card">
    <div class="brand">
      <span class="brand-mark"></span>
      <span class="brand-name">Ferncliff Advisory</span>
    </div>

    <div class="identity">
      <p class="person-name">Daniel Whitcombe</p>
      <p class="person-title">Founder / Principal</p>
    </div>

    <span class="divider-bar"></span>

    <ul class="contacts">
      <li>
        <svg viewBox="0 0 16 16" aria-hidden="true"><rect x="1" y="3" width="14" height="10" fill="#fff"/><path d="M1 3 L8 9 L15 3" fill="none" stroke="#1e1e84" stroke-width="1.5"/></svg>
        <span>dan@<strong>ferncliffadvisory</strong>.com</span>
      </li>
      <li>
        <svg viewBox="0 0 16 16" aria-hidden="true"><circle cx="8" cy="8" r="7" fill="#fff"/><g fill="none" stroke="#1e1e84" stroke-width="1.2"><ellipse cx="8" cy="8" rx="3" ry="7"/><path d="M1 8 H15 M2.5 4.5 H13.5 M2.5 11.5 H13.5"/></g></svg>
        <span>www.<strong>ferncliffadvisory</strong>.com</span>
      </li>
    </ul>

    <span class="rule"></span>

    <p class="address">2870 North 9th Avenue, Summit Floor, Elm Ridge, Illinois 60531</p>
  </main>
</body>
</html>
```